Simple and Clean business card design

We would like the design to be simple clean and to incorporate our colors.

We are open to your design and talent, we have the dots in our logo as we think of it as data points and we connect data points for people.

We are open to see the great creative and clean design you bring to the table

Contact Information for Business Card

please include: name, position, email, phone and website

Font styles to use
Sans Serif

Requirements
Must have
• my colors incorporated, simplicity
Nice to have
• lots of white space, simplicity
Should not have
• complexicity/ complex art

```html
<!DOCTYPE html>
<html lang="en">
<head>
<meta charset="utf-8">
<title>Lumera — Business Card</title>
<link rel="stylesheet" href="https://fonts.googleapis.com/css2?family=Work+Sans:wght@400;500;600;700&display=swap">
<style>
  :root {
    --stage: #e6e6e9;
    --card-white: #ffffff;
    --card-black: #050505;
    --ink: #111111;
    --blue: #5580c2;
    --green: #34a853;
    --yellow: #f6bf17;
    --red: #e8402f;
    --shadow: rgba(0, 0, 0, 0.22);
  }
  * { box-sizing: border-box; margin: 0; padding: 0; }
  html, body {
    width: 1200px;
    height: 881px;
    overflow: hidden;
    background: var(--stage);
    font-family: "Work Sans", Arial, sans-serif;
  }
  .canvas { position: relative; width: 1200px; height: 881px; }

  .card {
    position: absolute;
    width: 630px;
    height: 360px;
    border-radius: 24px;
    overflow: hidden;
    box-shadow: 0 14px 34px var(--shadow);
  }

  /* Back side */
  .card--back { left: 60px; top: 50px; background: var(--card-black); }
  .card--back .brand {
    position: absolute;
    left: 0; right: 0; top: 140px;
    display: flex;
    justify-content: center;
    align-items: center;
    gap: 16px;
  }
  .brand-dot {
    width: 26px; height: 26px;
    border-radius: 50%;
    background: var(--blue);
  }
  .brand-name {
    font-weight: 700;
    font-size: 72px;
    line-height: 1;
    letter-spacing: -1px;
  }
  .card--back .brand-name { color: #ffffff; }

  /* Front side */
  .card--front { left: 510px; top: 470px; background: var(--card-white); }
  .card--front .brand {
    position: absolute;
    left: 44px; top: 38px;
    display: flex;
    align-items: center;
    gap: 12px;
  }
  .card--front .brand-name { color: var(--ink); font-size: 58px; }
  .card--front .brand-dot { width: 20px; height: 20px; }

  .accent-bar {
    position: absolute;
    left: 0; top: 186px;
    width: 10px; height: 50px;
    background: var(--yellow);
  }

  .person { position: absolute; left: 44px; top: 128px; }
  .person-name {
    color: var(--blue);
    font-weight: 600;
    font-size: 24px;
    letter-spacing: 2.5px;
    text-transform: uppercase;
  }
  .person-role {
    color: var(--ink);
    font-size: 17px;
    letter-spacing: 1px;
    margin-top: 2px;
  }
  .address {
    color: var(--ink);
    font-size: 16px;
    letter-spacing: 1px;
    line-height: 1.3;
    margin-top: 12px;
  }
  .contacts { list-style: none; margin-top: 14px; }
  .contacts li {
    display: flex;
    align-items: center;
    gap: 10px;
    color: var(--ink);
    font-size: 16px;
    letter-spacing: 1px;
    line-height: 1.5;
  }
  .contacts svg { width: 14px; height: 14px; flex: none; }

  .feature-circle {
    position: absolute;
    right: 70px; top: 110px;
    width: 170px; height: 170px;
    border-radius: 50%;
    background: var(--blue);
  }
</style>
</head>
<body>
<main class="canvas">

  <section class="card card--back" aria-label="Card back">
    <div class="brand">
      <span class="brand-dot"></span>
      <span class="brand-name">Lumera</span>
    </div>
  </section>

  <section class="card card--front" aria-label="Card front">
    <div class="brand">
      <span class="brand-dot"></span>
      <span class="brand-name">Lumera</span>
    </div>

    <span class="accent-bar"></span>

    <div class="person">
      <h1 class="person-name">Daniel Reyes</h1>
      <p class="person-role">Founder</p>
      <p class="address">418 Cedar Hollow Lane<br>Austin, TX 78701</p>
      <ul class="contacts">
        <li>
          <svg viewBox="0 0 16 16" aria-hidden="true"><path d="M4 1.5l2.2 3-1.3 1.6c.9 2 2.4 3.5 4.4 4.4l1.6-1.3 3 2.2-1.2 2.6C7.3 13.8 2.2 8.7 1.4 3.2z" fill="var(--blue)"/></svg>
          0412 555 019
        </li>
        <li>
          <svg viewBox="0 0 16 16" aria-hidden="true"><rect x="1.5" y="3.5" width="13" height="9" rx="1" fill="none" stroke="var(--blue)" stroke-width="1.4"/><path d="M1.5 4l6.5 5 6.5-5" fill="none" stroke="var(--blue)" stroke-width="1.4"/></svg>
          hello@lumeradata.com
        </li>
        <li>
          <svg viewBox="0 0 16 16" aria-hidden="true"><g fill="none" stroke="var(--blue)" stroke-width="1.2"><circle cx="8" cy="8" r="6.5"/><ellipse cx="8" cy="8" rx="3" ry="6.5"/><path d="M1.5 8h13M2.5 4.8h11M2.5 11.2h11"/></g></svg>
          www.lumeradata.com
        </li>
      </ul>
    </div>

    <span class="feature-circle"></span>
  </section>

</main>
</body>
</html>
```